Corvane Capital Business Cards

These are professional business cards that are for my family office.
Put fake emails and phone numbers as of now until I finalize those components. This family office controls my families investments, assets, and future. The cards should be professional.
..
.
.
.
I just uploaded another variation of a logo I would like to see as a business card to I am inbeteen which logo to use

Target Market(s)

business

Industry/Entity Type

business

Contact Information for Business Card

Professional, wealth related, finance related.

Requirements
Must have
• Logo

```html
<!DOCTYPE html>
<html lang="en">
<head>
<meta charset="utf-8">
<title>Corvane Capital Business Cards</title>
<link rel="stylesheet" href="https://fonts.googleapis.com/css2?family=Cinzel:wght@500&family=Crimson+Text:wght@400&display=swap">
<style>
  :root {
    --backdrop: #5f5f61;
    --navy: #1b1f2b;
    --navy-deep: #151924;
    --ink: #1a1d28;
    --white: #ffffff;
    --grey: #9a9a9a;
    --grey-text: #8e8e8e;
    --icon: #8a8a8a;
  }
  * { margin: 0; padding: 0; box-sizing: border-box; }
  html, body { width: 900px; height: 1200px; overflow: hidden; }
  body { background: var(--backdrop); position: relative; }

  .card { position: absolute; left: 133px; width: 633px; height: 364px; overflow: hidden; }
  .card--front { top: 210px; background: var(--navy); }
  .card--back { top: 624px; background: var(--white); }

  .monogram-field {
    position: absolute; inset: 0;
    background: radial-gradient(ellipse at 50% 45%, #222736 0%, var(--navy) 55%, var(--navy-deep) 100%);
  }

  .front-mark {
    position: absolute; left: 275px; top: 135px;
    width: 82px; height: 82px; border-radius: 50%;
    border: 2px solid var(--white);
  }
  .front-name {
    position: absolute; left: 0; right: 0; top: 232px; text-align: center;
    font-family: "Cinzel", serif; font-weight: 500; font-size: 28px;
    color: var(--white); letter-spacing: 0.5px;
  }

  .back-mark {
    position: absolute; left: 113px; top: 100px;
    width: 118px; height: 118px; border-radius: 50%;
    border: 3px solid var(--ink);
  }
  .back-name {
    position: absolute; left: 30px; width: 285px; top: 228px; text-align: center;
    font-family: "Cinzel", serif; font-weight: 500; font-size: 28px;
    color: var(--ink); white-space: nowrap;
  }

  .divider { position: absolute; left: 316px; width: 2px; }
  .divider--top { top: 100px; height: 38px; background: var(--ink); }
  .divider--mid { top: 142px; height: 86px; background: var(--grey); width: 3px; }
  .divider--bottom { top: 231px; height: 37px; background: var(--ink); }

  .details { position: absolute; left: 347px; top: 94px; font-family: "Crimson Text", serif; color: var(--ink); }
  .person-name { font-family: "Cinzel", serif; font-weight: 500; font-size: 25px; line-height: 30px; letter-spacing: 0.3px; }
  .person-role { font-family: "Cinzel", serif; font-size: 14px; color: var(--grey-text); line-height: 18px; margin-bottom: 5px; }
  .address { font-size: 16.5px; line-height: 21px; margin-bottom: 6px; }
  .contact { list-style: none; font-size: 16px; }
  .contact li { display: flex; align-items: center; height: 25px; }
  .contact svg { width: 15px; height: 15px; margin-right: 9px; fill: var(--icon); }
  .phone-number { letter-spacing: 2px; }

  .footer-band { position: absolute; left: 0; bottom: 0; width: 633px; height: 13px; }
</style>
</head>
<body>

<section class="card card--front">
  <div class="monogram-field" role="img" aria-label="Embossed repeating brand pattern on dark navy"></div>
  <div class="front-mark"></div>
  <div class="front-name">Corvane Capital</div>
</section>

<section class="card card--back">
  <div class="back-mark"></div>
  <div class="back-name">Corvane Capital</div>

  <div class="divider divider--top"></div>
  <div class="divider divider--mid"></div>
  <div class="divider divider--bottom"></div>

  <div class="details">
    <div class="person-name">Ravin Deshmukh</div>
    <div class="person-role">CEO</div>
    <div class="address">412 N.Calloway Suite 5<br>Midland, Tx 79701</div>
    <ul class="contact">
      <li>
        <svg viewBox="0 0 16 16"><path d="M3.6 1.2l2.3 2.6c.4.4.3 1-.1 1.4L4.7 6.2c.9 2 2.6 3.8 4.7 4.8l1-1.1c.4-.4 1-.5 1.4-.1l2.6 2.2c.4.4.4 1 0 1.4l-1.3 1.3c-.6.6-1.5.8-2.3.5C6 13.6 2.5 10.1.9 5.2.6 4.4.8 3.5 1.4 2.9L2.2 1.2c.4-.4 1-.4 1.4 0z"/></svg>
        <span class="phone-number">(555)214-0387</span>
      </li>
      <li>
        <svg viewBox="0 0 16 16"><path d="M1 3h14v1.2L8 9 1 4.2z"/><path d="M1 5.6l7 4.8 7-4.8V13H1z"/></svg>
        <span>sales@corvanecapital.com</span>
      </li>
      <li>
        <svg viewBox="0 0 16 16"><path d="M8 1a7 7 0 100 14A7 7 0 008 1zm0 1.3c.7 0 1.6 1.3 2 3.2H6c.4-1.9 1.3-3.2 2-3.2zM5.8 6.8h4.4a11 11 0 010 2.4H5.8a11 11 0 010-2.4zM2.5 6.8h2a13 13 0 000 2.4h-2a5.7 5.7 0 010-2.4zm9 0h2a5.7 5.7 0 010 2.4h-2a13 13 0 000-2.4zM6 10.5h4c-.4 1.9-1.3 3.2-2 3.2s-1.6-1.3-2-3.2z"/></svg>
        <span>www.corvanecapital.com</span>
      </li>
    </ul>
  </div>

  <svg class="footer-band" viewBox="0 0 633 13" preserveAspectRatio="none">
    <polygon points="0,0 324,0 318,13 0,13" fill="var(--grey)"/>
    <polygon points="330,0 633,0 633,13 324,13" fill="var(--ink)"/>
  </svg>
</section>

</body>
</html>
```